Unique Business Card Design

Unique Business Card design for our orthotic and prosthetic company. Our logo is on our website, color is light blue. Unique shape (artificial leg shaped, vertical, etc..) preferred. Logo, business name, individual name and basic demographics needed.

Industry/Entity Type

Business

Contact Information for Business Card

Logo, Industry, Phone # Logo, "Prosthetic & Orthotic Services" Place to add individual name and contact info

Colors
cee9f5

Requirements
Must have
• The icon must be there, placement of "Prosthetic & Orthotic Services" can be moved
Nice to have
• Like the mix of light blue, and a little darker blue. One design included the icons from my website which was a nice touch

```html
<!DOCTYPE html>
<html lang="en">
<head>
<meta charset="utf-8">
<title>Limbworks Inc – Business Card</title>
<link href="https://fonts.googleapis.com/css2?family=Open+Sans:wght@400;600;700&family=Crimson+Text:ital@1&display=swap" rel="stylesheet">
<style>
  :root {
    --page-bg: #e9edf1;
    --card-bg: #f6f7f8;
    --brand-blue: #1a6fce;
    --panel-blue-light: #3a8ad8;
    --panel-blue-dark: #1b6ac6;
    --ink: #262626;
    --white: #ffffff;
  }
  * { margin: 0; padding: 0; box-sizing: border-box; }
  html, body {
    width: 1200px; height: 900px; overflow: hidden;
    background: var(--page-bg);
    font-family: "Open Sans", Arial, sans-serif;
  }
  .business-card {
    position: absolute; left: 145px; top: 170px;
    width: 910px; height: 560px;
    background: var(--card-bg);
    border-radius: 22px;
    overflow: hidden;
    box-shadow: 0 10px 30px rgba(0,0,0,0.12);
  }
  .contact-panel { position: absolute; inset: 0; width: 100%; height: 100%; }
  .brand-mark {
    position: absolute; left: 25px; top: 84px;
    width: 124px; height: 124px; border-radius: 50%;
    background: var(--brand-blue);
  }
  .brand-name {
    position: absolute; left: 200px; top: 108px;
    font-size: 36px; font-weight: 600; letter-spacing: 0.5px;
    color: var(--brand-blue); line-height: 1;
  }
  .brand-rule {
    position: absolute; left: 200px; top: 151px;
    width: 321px; height: 3px; background: var(--brand-blue);
  }
  .brand-tagline {
    position: absolute; left: 200px; top: 158px; width: 321px;
    text-align: center;
    font-family: "Crimson Text", Georgia, serif; font-style: italic;
    font-size: 20px; color: var(--brand-blue);
  }
  .person-name {
    position: absolute; left: 43px; top: 326px;
    font-size: 31px; font-weight: 700; color: var(--brand-blue);
  }
  .person-title {
    position: absolute; left: 43px; top: 366px;
    font-size: 23px; color: var(--ink);
  }
  .address {
    position: absolute; left: 45px; top: 432px;
    font-size: 23px; line-height: 29px; color: var(--ink);
  }
  .contact-list {
    position: absolute; right: 37px; top: 262px;
    list-style: none; text-align: right; color: var(--white);
  }
  .contact-item {
    display: flex; align-items: center; justify-content: flex-end;
    gap: 14px; font-size: 23px; line-height: 33px;
  }
  .contact-item--phone { font-size: 28px; font-weight: 600; line-height: 38px; }
  .contact-icon { width: 17px; height: 17px; flex: none; }
</style>
</head>
<body>
  <div class="business-card">
    <svg class="contact-panel" viewBox="0 0 650 400" preserveAspectRatio="none" aria-hidden="true">
      <defs>
        <linearGradient id="panelGradient" x1="0" y1="0" x2="1" y2="1">
          <stop offset="0" stop-color="var(--panel-blue-light)"/>
          <stop offset="1" stop-color="var(--panel-blue-dark)"/>
        </linearGradient>
      </defs>
      <path d="M418 0 C352 95 355 300 522 400 L650 400 L650 0 Z" fill="url(#panelGradient)"/>
    </svg>

    <div class="brand-mark"></div>
    <div class="brand-name">LIMBWORKS INC</div>
    <div class="brand-rule"></div>
    <div class="brand-tagline">Prosthetic &amp; Orthotic Services</div>

    <div class="person-name">DANIEL REYES</div>
    <div class="person-title">Managing Director</div>
    <div class="address">1234, Address Goes Here<br>Country Name, 123456</div>

    <ul class="contact-list">
      <li class="contact-item contact-item--phone">(555) 014-2280
        <svg class="contact-icon" viewBox="0 0 20 20"><path fill="#fff" d="M2 8c0-3 4-5 8-5s8 2 8 5l-3 1-1-2H6L5 9zM5 10h10l2 6H3z"/></svg>
      </li>
      <li class="contact-item">info@limbworksinc.com
        <svg class="contact-icon" viewBox="0 0 20 20"><rect x="2" y="4" width="16" height="12" fill="#fff"/><path d="M2 4l8 7 8-7" fill="none" stroke="#1b6ac6" stroke-width="1.5"/></svg>
      </li>
      <li class="contact-item">www.limbworksinc.com
        <svg class="contact-icon" viewBox="0 0 20 20"><circle cx="10" cy="10" r="8" fill="#fff"/><path d="M2 10h16M10 2c-4 4-4 12 0 16M10 2c4 4 4 12 0 16" fill="none" stroke="#1b6ac6" stroke-width="1.2"/></svg>
      </li>
    </ul>
  </div>
</body>
</html>
```